Bref créative
Safety products company
Safety products for life
Professional
Dorian K Pell
President/Founder
482 Quillmere Lane
Hollin Brook, PA 16328-4471
844.39R.GUMA (397.4862)
pell@vornatek.com
www.vornatek.com
BE PREPARED
HOME
DISASTER
CHILD
SENIOR
PET
TRAVEL
STAY PROTECTED
the logo
"stacked" logo - two more will be coming with white backgrounds as soon as I receive them
4 AI LOGOS

```html
<!DOCTYPE html>
<html lang="en">
<head>
<meta charset="utf-8">
<title>Vornatek Business Cards</title>
<link rel="stylesheet" href="https://fonts.googleapis.com/css2?family=Arimo:ital,wght@0,400;0,700;1,400&family=Michroma&display=swap">
<style>
  :root {
    --board: #2a2a2a;
    --card-dark: #3a3a3b;
    --card-light: #ffffff;
    --accent: #d8432a;
    --ink-light: #d4d4d4;
    --ink-dark: #5a5a5a;
    --ink-muted: #8c8c8c;
    --label: #d9d9d9;
    --divider-dark: #6a6a6a;
    --divider-light: #c8c8c8;
  }
  * { margin: 0; padding: 0; box-sizing: border-box; }
  html, body { width: 1200px; height: 838px; overflow: hidden; }
  body {
    background: var(--board);
    font-family: "Arimo", Arial, sans-serif;
    position: relative;
  }
  .card {
    position: absolute;
    width: 550px;
    height: 305px;
    overflow: hidden;
  }
  .card--dark { background: var(--card-dark); color: var(--ink-light); }
  .card--light { background: var(--card-light); color: var(--ink-dark); border-radius: 18px; }
  .pos-front-left  { left: 43px;  top: 43px; }
  .pos-front-right { left: 614px; top: 43px; }
  .pos-back-left   { left: 43px;  top: 454px; }
  .pos-back-right  { left: 614px; top: 454px; }

  .brand {
    position: absolute;
    left: 14px;
    top: 172px;
    width: 230px;
    display: flex;
    align-items: center;
    gap: 10px;
    font-size: 26px;
    font-weight: 700;
    letter-spacing: 1px;
  }
  .card--dark .brand { color: var(--ink-light); }
  .card--light .brand { color: var(--ink-muted); }
  .brand-dot {
    width: 16px; height: 16px; border-radius: 50%;
    background: var(--accent); flex: none;
  }
  .divider {
    position: absolute;
    left: 267px; top: 58px;
    width: 1px; height: 195px;
  }
  .card--dark .divider { background: var(--divider-dark); }
  .card--light .divider { background: var(--divider-light); }

  .details { position: absolute; left: 285px; top: 64px; }
  .person-name {
    color: var(--accent);
    font-style: italic;
    font-size: 18px;
    line-height: 20px;
  }
  .person-title { font-size: 13px; line-height: 18px; margin-bottom: 8px; }
  .contact-list { list-style: none; font-size: 11.5px; }
  .contact-list li { display: flex; align-items: center; height: 15px; }
  .contact-list svg { width: 10px; height: 10px; margin-right: 7px; fill: var(--accent); flex: none; }
  .contact-list .no-icon { padding-left: 17px; }

  .back-mark {
    position: absolute;
    left: 0; right: 0; top: 120px;
    display: flex; justify-content: center; align-items: center; gap: 12px;
    font-size: 34px; font-weight: 700; letter-spacing: 2px;
    color: var(--accent);
  }
  .back-mark .brand-dot { width: 22px; height: 22px; }
  .tagline {
    position: absolute;
    left: 0; right: 0; top: 218px;
    text-align: center;
    font-size: 15px;
    line-height: 28px;
  }
  .card--dark .tagline { color: var(--ink-muted); }
  .card--light .tagline { color: var(--ink-dark); }

  .label {
    position: absolute;
    width: 550px;
    text-align: center;
    font-family: "Michroma", Arial, sans-serif;
    font-size: 18px;
    letter-spacing: 2px;
    color: var(--label);
  }
  .label-front-left  { left: 43px;  top: 364px; }
  .label-front-right { left: 614px; top: 364px; }
  .label-back-left   { left: 43px;  top: 774px; }
  .label-back-right  { left: 614px; top: 774px; }
</style>
</head>
<body>
<svg width="0" height="0" style="position:absolute">
  <defs>
    <symbol id="icon-phone" viewBox="0 0 10 10"><path d="M2 0.5 L3.6 2.6 L2.8 3.6 Q4 6 6.4 7.2 L7.4 6.4 L9.5 8 L8.4 9.5 Q3 9 0.5 1.6 Z"/></symbol>
    <symbol id="icon-mobile" viewBox="0 0 10 10"><rect x="2.5" y="0" width="5" height="10" rx="1"/></symbol>
    <symbol id="icon-fax" viewBox="0 0 10 10"><rect x="0" y="3" width="10" height="5" rx="1"/><rect x="2.5" y="0" width="5" height="3"/></symbol>
    <symbol id="icon-mail" viewBox="0 0 10 10"><rect x="0" y="2" width="10" height="6.5" rx="1"/></symbol>
    <symbol id="icon-web" viewBox="0 0 10 10"><circle cx="5" cy="5" r="4.5"/></symbol>
    <symbol id="icon-pin" viewBox="0 0 10 10"><path d="M5 0 A3.6 3.6 0 0 1 8.6 3.6 Q8.6 6 5 10 Q1.4 6 1.4 3.6 A3.6 3.6 0 0 1 5 0 Z"/></symbol>
  </defs>
</svg>

<section class="card card--dark pos-front-left">
  <div class="brand"><span class="brand-dot"></span>VORNATEK</div>
  <div class="divider"></div>
  <div class="details">
    <p class="person-name">Dorian K Pell</p>
    <p class="person-title">President | Founder</p>
    <ul class="contact-list">
      <li><svg><use href="#icon-phone"/></svg>844.39R.GUMA (397.4862)</li>
      <li><svg><use href="#icon-phone"/></svg>844.397.4863</li>
      <li><svg><use href="#icon-mobile"/></svg>724.518.2096</li>
      <li><svg><use href="#icon-fax"/></svg>724.806.3317</li>
      <li><svg><use href="#icon-mail"/></svg>pell@vornatek.com</li>
      <li><svg><use href="#icon-web"/></svg>www.vornatek.com</li>
      <li><svg><use href="#icon-pin"/></svg>482 Quillmere Lane</li>
      <li class="no-icon">Hollin Brook, PA 16328-4471</li>
    </ul>
  </div>
</section>

<section class="card card--light pos-front-right">
  <div class="brand"><span class="brand-dot"></span>VORNATEK</div>
  <div class="divider"></div>
  <div class="details">
    <p class="person-name">Dorian K Pell</p>
    <p class="person-title">President | Founder</p>
    <ul class="contact-list">
      <li><svg><use href="#icon-phone"/></svg>844.39R.GUMA (397.4862)</li>
      <li><svg><use href="#icon-phone"/></svg>844.397.4863</li>
      <li><svg><use href="#icon-mobile"/></svg>724.518.2096</li>
      <li><svg><use href="#icon-fax"/></svg>724.806.3317</li>
      <li><svg><use href="#icon-mail"/></svg>pell@vornatek.com</li>
      <li><svg><use href="#icon-web"/></svg>www.vornatek.com</li>
      <li><svg><use href="#icon-pin"/></svg>482 Quillmere Lane</li>
      <li class="no-icon">Hollin Brook, PA 16328-4471</li>
    </ul>
  </div>
</section>

<p class="label label-front-left">BUSINESS CARD FRONT</p>
<p class="label label-front-right">BUSINESS CARD FRONT</p>

<section class="card card--dark pos-back-left">
  <div class="back-mark"><span class="brand-dot"></span>VORNATEK</div>
  <p class="tagline">Be Prepared | Home | Disaster | Child | Senior | Pet<br>Travel | Stay Protected</p>
</section>

<section class="card card--light pos-back-right">
  <div class="back-mark"><span class="brand-dot"></span>VORNATEK</div>
  <p class="tagline">Be Prepared | Home | Disaster | Child | Senior | Pet<br>Travel | Stay Protected</p>
</section>

<p class="label label-back-left">BUSINESS CARD BACK</p>
<p class="label label-back-right">BUSINESS CARD BACK</p>
</body>
</html>
```